Business Card Makeover. Recreate a sleek modern design for our business card.

DO NOT COPY OUR CURRENT DESIGN. MUST BE ONE SIDED BUSINESS CARD.
Create a new business card design, using our new logo. Attached is a sample of our current design and new logo. Please note the address and email will change. The new address is 412 Corvell West Palm Beach 33401 and our website will be www.delmarhollis.example.

We are an architectural and interior design firm. We prefer a clean modern look. Something that is refined and emulates excellence.

Industry/Entity Type

Architecture

Contact Information for Business Card

clean modern look, please do not copy our attached design.

Font styles to use
Other font styles liked:
• see attached business card font

Colors

Designer to choose colors to be used in the design.

Requirements
Must have
• Must have a modern appeal and resemble our current branding.
Nice to have
• modern font, our logo, legible name and titles progressive design
Should not have
• Do not add colors not reflected in our branding. Should not look like our current card.

```html
<!DOCTYPE html>
<html lang="en">
<head>
<meta charset="utf-8">
<title>Delmar Hollis Business Card</title>
<link href="https://fonts.googleapis.com/css2?family=Tinos:wght@700&family=Poppins:ital,wght@1,300&family=Roboto:wght@400&display=swap" rel="stylesheet">
<style>
  :root {
    --brand-blue: #0057b8;
    --card-white: #ffffff;
    --text-gray: #858585;
    --logo-gray: #2a2a2a;
    --backdrop: #e9e9e9;
  }
  html, body {
    margin: 0;
    padding: 0;
    width: 1125px;
    height: 1200px;
    overflow: hidden;
    background: var(--backdrop);
  }
  .card {
    position: absolute;
    left: 50px;
    top: 308px;
    width: 1025px;
    height: 584px;
    background: var(--card-white);
    overflow: hidden;
    font-family: "Roboto", sans-serif;
  }
  .card__band {
    position: absolute;
    left: 0;
    top: 332px;
    width: 100%;
    height: 252px;
    background: var(--brand-blue);
  }
  .person__name {
    position: absolute;
    left: 56px;
    top: 56px;
    margin: 0;
    font-family: "Tinos", serif;
    font-weight: 700;
    font-size: 41px;
    line-height: 1;
    color: var(--brand-blue);
    letter-spacing: 0.3px;
  }
  .person__title {
    position: absolute;
    left: 56px;
    top: 110px;
    margin: 0;
    font-family: "Poppins", sans-serif;
    font-style: italic;
    font-weight: 300;
    font-size: 23px;
    line-height: 1;
    color: var(--text-gray);
  }
  .firm-name {
    position: absolute;
    right: 49px;
    top: 68px;
    margin: 0;
    display: flex;
    align-items: center;
    gap: 12px;
    font-family: "Roboto", sans-serif;
    font-weight: 400;
    font-size: 42px;
    line-height: 1;
    color: var(--logo-gray);
    letter-spacing: 1px;
  }
  .firm-name__mark {
    width: 22px;
    height: 22px;
    border-radius: 50%;
    background: var(--brand-blue);
  }
  .details {
    position: absolute;
    left: 56px;
    top: 236px;
    margin: 0;
    font-size: 24px;
    line-height: 36px;
    color: var(--text-gray);
    font-style: normal;
  }
  .contacts {
    position: absolute;
    left: 56px;
    top: 374px;
    margin: 0;
    padding: 0;
    list-style: none;
    color: var(--card-white);
    font-size: 24px;
  }
  .contacts__item {
    display: flex;
    align-items: center;
    height: 34.5px;
  }
  .contacts__icon {
    width: 18px;
    height: 18px;
    margin-right: 14px;
    fill: var(--card-white);
  }
  .practice {
    position: absolute;
    right: 56px;
    top: 510px;
    margin: 0;
    font-size: 25px;
    line-height: 1;
    color: var(--card-white);
    letter-spacing: 0.3px;
  }
</style>
</head>
<body>
  <main class="card">
    <div class="card__band"></div>

    <h1 class="person__name">Graham Whitfield</h1>
    <p class="person__title">Partner / Director of Design</p>

    <p class="firm-name"><span class="firm-name__mark"></span>DELMAR HOLLIS</p>

    <address class="details">
      LIC.# AA26004817<br>
      412 Corvell West Palm Beach 33401
    </address>

    <ul class="contacts">
      <li class="contacts__item">
        <svg class="contacts__icon" viewBox="0 0 24 24" aria-hidden="true"><path d="M6.6 10.8c1.4 2.8 3.8 5.1 6.6 6.6l2.2-2.2c.3-.3.7-.4 1-.2 1.1.4 2.3.6 3.6.6.6 0 1 .4 1 1V20c0 .6-.4 1-1 1C10.6 21 3 13.4 3 4c0-.6.4-1 1-1h3.5c.6 0 1 .4 1 1 0 1.3.2 2.5.6 3.6.1.3 0 .7-.2 1L6.6 10.8z"/></svg>
        561.555.0142
      </li>
      <li class="contacts__item">
        <svg class="contacts__icon" viewBox="0 0 24 24" aria-hidden="true"><path d="M6 2h12v5H6zM3 8h18c1.1 0 2 .9 2 2v7h-4v5H5v-5H1v-7c0-1.1.9-2 2-2zm4 8v4h10v-4z"/></svg>
        561.555.0187
      </li>
      <li class="contacts__item">
        <svg class="contacts__icon" viewBox="0 0 24 24" aria-hidden="true"><path d="M7 1h10c1.1 0 2 .9 2 2v18c0 1.1-.9 2-2 2H7c-1.1 0-2-.9-2-2V3c0-1.1.9-2 2-2zm0 3v14h10V4zm5 15.5a1.2 1.2 0 100 2.4 1.2 1.2 0 000-2.4z"/></svg>
        561.555.0163
      </li>
      <li class="contacts__item">
        <svg class="contacts__icon" viewBox="0 0 24 24" aria-hidden="true"><path d="M2 4h20v16H2zm2 3v11h16V7l-8 6z"/></svg>
        graham@delmarhollis.example
      </li>
      <li class="contacts__item">
        <svg class="contacts__icon" viewBox="0 0 24 24" aria-hidden="true"><path d="M12 2a10 10 0 100 20 10 10 0 000-20zm-1 17.9A8 8 0 014.2 10L9 15v1c0 1.1.9 2 2 2zm6.9-2.5c-.3-.8-1-1.4-1.9-1.4h-1v-3c0-.6-.4-1-1-1H8v-2h2c.6 0 1-.4 1-1V7h2c1.1 0 2-.9 2-2v-.4a8 8 0 012.9 12.8z"/></svg>
        www.delmarhollis.example
      </li>
    </ul>

    <p class="practice">Architecture + Interior Design</p>
  </main>
</body>
</html>
```